Software Platform User Guide (Manual)

We need a user manual template for our online e-learning platform, Lanthorn, which allows users to create their own online courses.

We’re looking for a template for a few pages, including a cover, back page, table of contents, and pages for text-only (or bullet points), and text & images (screenshots). We would like to be able to add new pages and adjust textual content ourselves. Lorem ipsum is totally cool as placeholder text. The name of the product is Lanthorn, but the company name is Cordwain Meridian, so we would like the cover and back cover to say “Cordwain Meridian" and "Lanthorn".

We have uploaded a few files to give you a sense of our color scheme and logo. You can also check out our website at cmvista.example for an idea of our aesthetic sensibility. The design should be simple and elegant, and (being a user manual) clarity is king. We use Avenir and Elizabeth as or primary fonts. We have also uploaded some sample screen shots from Lanthorn. You can use those screenshots to help direct your work, but note that the interface design is changing soon; i.e., you should emphasize the Cordwain Meridian brand aesthetic more so than the Lanthorn user interface design.

Target Market(s)

Businesses and nonprofits looking to implement our platform. Many buyers are female, but the people reading the manual are typically male.

Industry/Entity Type

It Company

Requirements
Must have
• The final product must be a template that will work in Microsoft Word, PowerPoint, or Apple Keynote/Pages. It's fine to send PDFs for previews. Note we need the final product in ONE of the above choices (Word, Powerpoint, Keynote, or Pages), not ALL.

You must make use of the CM logo and fonts on every page. Note that the tag line, "quickest bridge across two shores of thought" in one version of the logo does note have to be included.

We need clear delineation between headers, sub-headers, and bullets, as well as a great looking cover, table of contents and back page.

Please Note: Please disregard the OLUD logo on any screenshots. These were mockups for a client. Please don't use the OLUD name or logo.

```html
<!DOCTYPE html>
<html lang="en">
<head>
<meta charset="utf-8">
<title>Cordwain Meridian – Lanthorn User Guide Cover</title>
<link href="https://fonts.googleapis.com/css2?family=Tinos&family=Mulish:wght@300&display=swap" rel="stylesheet">
<style>
  :root {
    --ink: #231f20;
    --brand-blue: #4a8cce;
    --brand-green: #b5d334;
    --paper: #ffffff;
    --sky-light: #f2f5f8;
    --sky-mid: #c9d9ea;
    --serif: "Tinos", "Times New Roman", serif;
    --sans: "Mulish", "Avenir", sans-serif;
  }
  * { margin: 0; padding: 0; box-sizing: border-box; }
  html, body { width: 809px; height: 1200px; overflow: hidden; background: var(--ink); }
  .cover {
    position: relative;
    width: 809px;
    height: 1200px;
    background: var(--ink);
    overflow: hidden;
  }
  .brand-lockup {
    position: absolute;
    left: 95px;
    top: 196px;
  }
  .brand-lockup__name {
    display: flex;
    align-items: center;
    gap: 10px;
    font-family: var(--serif);
    font-size: 24px;
    letter-spacing: 3px;
    color: var(--brand-blue);
  }
  .brand-lockup__mark {
    width: 12px;
    height: 12px;
    background: var(--brand-blue);
  }
  .brand-lockup__tagline {
    margin-top: 6px;
    font-family: var(--sans);
    font-weight: 300;
    font-size: 13px;
    color: var(--brand-green);
  }
  .cover-title {
    position: absolute;
    right: 65px;
    top: 328px;
    text-align: right;
  }
  .cover-title__company {
    font-family: var(--serif);
    font-size: 32px;
    color: var(--paper);
  }
  .cover-title__tagline {
    margin-top: 10px;
    font-family: var(--serif);
    font-size: 22px;
    letter-spacing: 2px;
    color: var(--brand-green);
  }
  .cover-photo {
    position: absolute;
    left: 18px;
    top: 444px;
    width: 773px;
    height: 540px;
    background: linear-gradient(160deg, var(--sky-mid) 0%, var(--sky-light) 45%, var(--paper) 100%);
  }
  .product-tab {
    position: absolute;
    left: 0;
    top: 0;
    width: 809px;
    height: 1200px;
    pointer-events: none;
  }
  .product-name {
    position: absolute;
    left: 500px;
    top: 478px;
    width: 290px;
    text-align: center;
    font-family: var(--serif);
    font-size: 54px;
    letter-spacing: 4px;
    color: var(--paper);
  }
  .cover-url {
    position: absolute;
    right: 82px;
    top: 1128px;
    font-family: var(--serif);
    font-size: 22px;
    letter-spacing: 4px;
    color: var(--paper);
  }
</style>
</head>
<body>
<main class="cover">
  <header class="brand-lockup">
    <div class="brand-lockup__name"><span class="brand-lockup__mark"></span>Cordwain Meridian</div>
    <div class="brand-lockup__tagline">the quickest bridge across two shores of thought</div>
  </header>

  <section class="cover-title">
    <h1 class="cover-title__company">Cordwain Meridian</h1>
    <p class="cover-title__tagline">quickest bridge across two shores of thought</p>
  </section>

  <div class="cover-photo" role="img" aria-label="Photo of a stack of notebooks and a computer mouse on a white desk against a pale sky"></div>

  <svg class="product-tab" viewBox="0 0 809 1200" aria-hidden="true">
    <polygon points="470,446 461,430 802,430 802,582 550,674" fill="var(--brand-blue)"/>
    <polygon points="0,1164 128,1122 154,1200 0,1200" fill="var(--brand-green)"/>
  </svg>

  <h2 class="product-name">Lanthorn</h2>

  <p class="cover-url">www. cmvista.example</p>
</main>
</body>
</html>
```